Gymnastics and fitness web design

Valdrey Gymnastics and fitness centre is opening a new branch in the United States.
Target Audience:
22 to 40 year old people who are not satisfied with their current body figure, shape and size.
and
Our programs
VoltaRig, Sports performance and personal training
DESIGN STYLE:
We want the site to be trendy, edgy and cool. The colors we prefer are blue, black and silver. Th idea is people should get motivated by seeing our website. We don't like adding many text in the design, images oriented design is what we are after.
Contents should be added-
Slider
who we are?
section for our programs
Why us?
Video showing some tutorials
Articles
contact us form with map, Address, Phone number, timings, and social media buttons.

```html
<!DOCTYPE html>
<html lang="en">
<head>
<meta charset="utf-8">
<title>Valdrey Gymnastics – Recent Posts &amp; Contact</title>
<link href="https://fonts.googleapis.com/css2?family=Open+Sans:wght@300;400;600&display=swap" rel="stylesheet">
<style>
  :root {
    --navy: #323846;
    --blue: #2ea3dc;
    --ink: #333333;
    --muted: #b9bcc4;
    --white: #ffffff;
    --line: #d8d8d8;
    --field: #5b5b5b;
    --btn-grey: #6d6f73;
  }
  * { margin: 0; padding: 0; box-sizing: border-box; }
  html, body { width: 1200px; height: 763px; overflow: hidden; }
  body { font-family: "Open Sans", Arial, sans-serif; color: var(--ink); background: var(--white); position: relative; }
  .abs { position: absolute; }

  .posts { left: 0; top: 0; width: 1200px; height: 312px; background: var(--navy); }
  .section-title { width: 1200px; left: 0; text-align: center; font-size: 26px; font-weight: 600; letter-spacing: 0.3px; }
  .section-title .accent { color: var(--blue); }
  .posts .section-title { top: 11px; color: var(--white); }
  .title-rule { left: 567px; width: 67px; height: 2px; background: var(--blue); }

  .post-photo { width: 215px; height: 171px; top: 85px; }
  .photo-produce { left: 112px; background: linear-gradient(135deg, #e8c53a 0%, #6c9a2c 40%, #3f7a2a 65%, #c9402c 100%); }
  .photo-workout { left: 613px; background: linear-gradient(160deg, #5a5e66 0%, #9fa3a8 45%, #c9ccd0 70%, #6b6e73 100%); }
  .post-body { top: 83px; width: 260px; color: var(--white); }
  .post-title { font-size: 12.5px; line-height: 18px; }
  .post-meta { font-size: 10px; color: var(--muted); margin-top: 1px; }
  .post-text { font-size: 11px; line-height: 15.5px; margin-top: 12px; }
  .btn-read { display: inline-block; margin-top: 11px; background: var(--btn-grey); color: var(--white); font-size: 10.5px; padding: 4px 10px; border: 1px solid #8a8c90; }

  .contact .section-title { top: 337px; color: var(--ink); }
  .map { left: 112px; top: 398px; width: 474px; height: 159px; background: linear-gradient(120deg, #d8d2c6 0%, #e6e1d8 50%, #d6cfc2 100%); }
  .field { border: 1px solid var(--field); font-size: 11.5px; color: #555; font-weight: 300; padding: 5px 8px; background: var(--white); }
  .btn-blue { background: var(--blue); color: var(--white); font-size: 11.5px; text-align: center; }
  .divider { left: 0; top: 577px; width: 1200px; height: 1px; background: var(--line); }

  .foot-head { font-size: 11px; color: var(--ink); }
  .foot-item { font-size: 11px; color: #444; display: flex; align-items: center; gap: 7px; }
  .foot-item svg { width: 11px; height: 11px; fill: #333; }
  .social { display: flex; gap: 11px; top: 623px; left: 671px; }
  .social span { width: 17px; height: 17px; background: #333; border-radius: 3px; }

  .copyright-bar { left: 0; top: 735px; width: 1200px; height: 28px; background: var(--navy); color: var(--white); font-size: 11px; padding: 6px 0 0 113px; }
</style>
</head>
<body>

<section class="posts abs">
  <h2 class="section-title abs">RECENT <span class="accent">POSTS</span></h2>
  <div class="title-rule abs" style="top:51px"></div>

  <div class="post-photo photo-produce abs" role="img" aria-label="Photo of fresh vegetables: corn, peppers, leeks and green beans"></div>
  <article class="post-body abs" style="left:340px">
    <h3 class="post-title" style="font-weight:400">Eat Vegetables to have a live a long life</h3>
    <p class="post-meta">Feb 19, 2017 · by Valdrey</p>
    <p class="post-text">Lorem ipsum dolor sit amet, consectetur adipiscing elit. Ut volutpat rutrum eros sit amet sollicitudin. Suspendisse pulvinar velit nec.</p>
    <span class="btn-read">READ MORE</span>
  </article>

  <div class="post-photo photo-workout abs" role="img" aria-label="Photo of two athletes doing push-ups on dumbbells in a gym"></div>
  <article class="post-body abs" style="left:841px">
    <h3 class="post-title" style="font-weight:400">Dumbells make you slim</h3>
    <p class="post-meta">Feb 19, 2017 · by Valdrey</p>
    <p class="post-text">Lorem ipsum dolor sit amet, consectetur adipiscing elit. Ut volutpat rutrum eros sit amet sollicitudin. Suspendisse pulvinar velit nec.</p>
    <span class="btn-read">READ MORE</span>
  </article>
</section>

<section class="contact">
  <h2 class="section-title abs">CONTACT <span class="accent">US</span></h2>
  <div class="title-rule abs" style="top:377px"></div>

  <div class="map abs" role="img" aria-label="Street map showing the gym location marked with a pin"></div>

  <div class="field abs" style="left:614px;top:400px;width:225px;height:26px">Name</div>
  <div class="field abs" style="left:614px;top:444px;width:225px;height:26px">Email Address</div>
  <div class="field abs" style="left:614px;top:487px;width:225px;height:26px">Mobile Number</div>
  <div class="field abs" style="left:849px;top:400px;width:251px;height:113px">Message</div>
  <div class="btn-blue abs" style="left:614px;top:531px;width:63px;height:26px;line-height:26px">SUBMIT</div>
</section>

<div class="divider abs"></div>

<footer>
  <h4 class="foot-head abs" style="left:112px;top:599px;font-weight:400">LOCATION</h4>
  <p class="foot-item abs" style="left:112px;top:627px">
    <svg viewBox="0 0 12 12"><path d="M6 0a4 4 0 0 0-4 4c0 3 4 8 4 8s4-5 4-8a4 4 0 0 0-4-4zm0 5.6A1.6 1.6 0 1 1 6 2.4a1.6 1.6 0 0 1 0 3.2z"/></svg>
    214 Harlow Avenue Brenmoor, MD 21098</p>
  <p class="foot-item abs" style="left:112px;top:652px">
    <svg viewBox="0 0 12 12"><path d="M2.4 0.6l2 2.2-1.2 1.4a7 7 0 0 0 4.6 4.6l1.4-1.2 2.2 2-1.3 1.8C5 11 1 7 0.6 1.9z"/></svg>
    PHONE:+1 410 555 0187</p>
  <p class="foot-item abs" style="left:112px;top:677px">
    <svg viewBox="0 0 12 12"><path d="M0.5 2h11v8h-11z" fill="none" stroke="#333" stroke-width="1"/><path d="M0.5 2.5l5.5 4 5.5-4" fill="none" stroke="#333" stroke-width="1"/></svg>
    HELLO@VALDREY.FIT</p>

  <h4 class="foot-head abs" style="left:420px;top:599px;font-weight:400">WORKING HOURS:</h4>
  <p class="foot-item abs" style="left:420px;top:625px">Mon-Frifrom 8:00am to 9:00pm</p>
  <p class="foot-item abs" style="left:420px;top:651px">Sat-Sunfrom 10:00am to 6:00pm</p>

  <h4 class="foot-head abs" style="left:671px;top:597px;font-weight:400">SOCIAL NETWORKS:</h4>
  <div class="social abs" aria-label="Social network links">
    <span></span><span></span><span></span><span></span><span></span>
  </div>

  <h4 class="foot-head abs" style="left:849px;top:595px;font-weight:400">NEWSLETTER</h4>
  <div class="field abs" style="left:849px;top:615px;width:226px;height:26px">Email Address</div>
  <div class="btn-blue abs" style="left:849px;top:650px;width:80px;height:26px;line-height:26px">SUBSCRIBE</div>

  <div class="copyright-bar abs">Copyright © 2017 Designed by Valdrey Gymnastics</div>
</footer>

</body>
</html>
```